DJ Colm Vetter

I'm looking for a professional but still artsy/progressive design. I come from a hip hop/club DJ background playing a lot of underground music but have switched to doing more corporate parties and weddings recently. I am all about keeping the dancefloor moving and emotionally connecting with the crowd. I'd like a trendy/updated color palette. Something that's clean enough that looks professional but also trendy enough to convey that by the end of the night we'll be sweatily dancing to the latest hits. Some designers/artists I like: Tarn Olquist, Pavel Remy, Wendell Quarrie, Lumeno 7400, Silas Dravin.

```html
<!DOCTYPE html>
<html lang="en">
<head>
<meta charset="utf-8">
<title>DJ Colm Vetter — Business Card</title>
<link href="https://fonts.googleapis.com/css2?family=Noto+Serif:wght@400;700&display=swap" rel="stylesheet">
<style>
  :root {
    --backdrop: #e9e6e1;
    --card-black: #06070b;
    --card-navy: #0d1222;
    --photo-deep: #0b101d;
    --photo-shirt: #1e2a48;
    --photo-warm: #6a5a52;
    --photo-haze: #3c4258;
    --photo-blue: #2b4a8c;
    --photo-red: #8a2a33;
    --ink-white: #f4f4f6;
  }
  html, body {
    margin: 0;
    padding: 0;
    width: 1200px;
    height: 1023px;
    overflow: hidden;
    background: var(--backdrop);
  }
  .stage {
    width: 1200px;
    height: 1023px;
    display: flex;
    align-items: center;
    justify-content: center;
  }
  .card {
    position: relative;
    width: 980px;
    height: 560px;
    border-radius: 30px;
    overflow: hidden;
    background: linear-gradient(160deg, var(--card-navy) 0%, var(--card-black) 75%);
    box-shadow: 0 22px 46px rgba(0,0,0,0.28);
    font-family: "Noto Serif", Georgia, serif;
    color: var(--ink-white);
  }
  .card__photo {
    position: absolute;
    inset: 0;
    background:
      radial-gradient(ellipse 16% 20% at 30% 30%, var(--photo-warm) 0%, transparent 80%),
      radial-gradient(ellipse 34% 30% at 50% 40%, var(--photo-shirt) 0%, transparent 85%),
      radial-gradient(ellipse 14% 10% at 72% 78%, var(--photo-red) 0%, transparent 90%),
      radial-gradient(ellipse 22% 14% at 62% 82%, var(--photo-blue) 0%, transparent 90%),
      radial-gradient(ellipse 20% 12% at 20% 80%, rgba(60,110,90,0.55) 0%, transparent 90%),
      radial-gradient(ellipse 60% 40% at 55% 85%, var(--photo-haze) 0%, transparent 80%),
      radial-gradient(ellipse 55% 70% at 38% 45%, var(--photo-haze) 0%, transparent 80%),
      radial-gradient(ellipse 10% 10% at 80% 18%, rgba(90,120,140,0.5) 0%, transparent 90%),
      linear-gradient(180deg, var(--photo-deep) 0%, var(--card-black) 100%);
  }
  .card__shade {
    position: absolute;
    inset: 0;
    background: linear-gradient(90deg, transparent 55%, rgba(4,5,9,0.75) 100%),
                linear-gradient(0deg, rgba(4,5,9,0.55) 0%, transparent 35%);
  }
  .card__sheen {
    position: absolute;
    inset: 0;
    background: linear-gradient(100deg, rgba(255,255,255,0.16) 0%, rgba(255,255,255,0.10) 28%, rgba(255,255,255,0.03) 45%, transparent 58%);
  }
  .card__name {
    position: absolute;
    top: 30px;
    left: 44px;
    margin: 0;
    font-size: 40px;
    font-weight: 400;
    letter-spacing: 1px;
    text-transform: uppercase;
    text-shadow: 0 1px 3px rgba(0,0,0,0.6);
  }
  .card__contact {
    position: absolute;
    right: 48px;
    bottom: 34px;
    margin: 0;
    padding: 0;
    list-style: none;
    font-size: 25px;
    line-height: 1.5;
    text-shadow: 0 1px 3px rgba(0,0,0,0.6);
  }
</style>
</head>
<body>
  <main class="stage">
    <article class="card">
      <div class="card__photo" role="img" aria-label="Photo of the DJ in a dark club, smiling behind a lit mixing deck with headphones around his neck"></div>
      <div class="card__shade"></div>
      <div class="card__sheen"></div>
      <h1 class="card__name">DJ Colm Vetter</h1>
      <ul class="card__contact">
        <li>P : +330 5718-3046</li>
        <li>E : info@DJColmVetter.com</li>
        <li>W : nightlatitude.com</li>
      </ul>
    </article>
  </main>
</body>
</html>
```